Website for Architecture & Interior Design firm

We are architecture and interior design firm looking for website design, word press based, smooth, elegant and easy to use for visitors. It should be easy to navigate using a mobile phone, with the ability to change pictures easily. It is a Bilingual website, (English: left to right, Arabic: right to left). A button in the menu bar is required to change the language, At first, we expect an English version, then we will help the designer by providing Arabic translation for any part of the website. Our website main purpose is to display our works in a picture format (Portfolio) to our clients, which mainly consist of four galleries from our (Services) as follow: 1- Architecture 2- Interior Design 3- Project Management 4- Importing from Abroad - Each service will have its page, which displays projects(items) in thumbnail format with simple text, which deploys (when clicked) into Fullscreen gallery to show the items related pictures (Dark gray or black background). - Navigation buttons/arrows are required, (X) button to close the navigation. - This is a very important part, the user experience in PC/Browser mode or Mobile mode should be easy, error-free and fast. Our homepage consists of four main elements: A- Edge to edge picture (Changing in a smooth transitional way, Random pictures from our Services) with our Logo, also persistent menu bar in the top (Home | About Us | Architecture | Interior design | Project Management | Importing from Abroad) + Social media icons B- Photo tiles (Random pictures from our Services) C- Our Services in a fixed 4-tile picture (Clickable) D- Contact Section (Simple name, contact number, message form) We expect the final service should be: 1- a fully functioning website, WordPress based, ready to be used by visitors 2- full content filling, we will contact the designer and provide the material (texture, text,etc..)
Colors
Designer to choose colors to be used in the design.
Look and feel
Each slider illustrates characteristics of the customer's brand and the style your logo design should communicate.

```html
<!DOCTYPE html>
<html lang="en">
<head>
<meta charset="utf-8">
<title>K &amp; M Studio — Architecture &amp; Interior Design</title>
<link href="https://fonts.googleapis.com/css2?family=Arimo:wght@400;700&family=Open+Sans:wght@400&display=swap" rel="stylesheet">
<style>
:root{
  --navy:#1d2240;
  --ink:#111428;
  --gold:#b5832b;
  --gold-light:#d4a649;
  --white:#ffffff;
  --lavender:#e3e6f3;
  --field-border:#c9ccd8;
  --text:#222;
}
*{margin:0;padding:0;box-sizing:border-box}
html,body{width:1200px;height:3322px;overflow:hidden}
body{position:relative;background:var(--white);font-family:"Arimo",Arial,sans-serif;color:var(--text)}
.abs{position:absolute}

/* Hero */
.hero{left:0;top:0;width:1200px;height:762px;background:linear-gradient(180deg,#2a3566 0%,#3a3350 30%,#4b3a3c 55%,#2a2a3a 100%)}
.brand{left:62px;top:30px;color:var(--white);font-size:32px;line-height:34px;font-weight:700;letter-spacing:1px}
.brand span{display:block;font-weight:700}
.nav{top:66px;right:40px;display:flex;gap:27px;font-size:14px;font-weight:700;color:var(--white)}
.nav .active{color:var(--gold-light);position:relative}
.nav .active::after{content:"";position:absolute;left:0;right:0;bottom:-10px;height:3px;background:var(--white)}
.social{display:flex;gap:26px}
.social i{display:block;width:22px;height:22px;border-radius:50%;background:var(--white)}
.hero-social{left:838px;top:20px}
.lang{left:1040px;top:14px;width:82px;height:33px;border:1px solid rgba(255,255,255,.7);color:var(--white);font-size:13px;display:flex;align-items:center;justify-content:center;gap:6px}
.welcome{left:0;width:1200px;top:258px;text-align:center;color:var(--white);font-size:46px;letter-spacing:-1px}
.hero-title{left:0;width:1200px;top:314px;text-align:center;color:var(--white);font-size:82px;font-weight:700;letter-spacing:-1px}
.btn{display:flex;align-items:center;justify-content:center;color:var(--white);font-weight:700;background:linear-gradient(90deg,var(--gold),var(--gold-light))}
.btn-start{left:492px;top:414px;width:207px;height:53px;font-size:19px}
.hero-curve{left:0;top:640px}

/* Section headings */
.heading{left:0;width:1200px;text-align:center;font-size:36px;font-weight:700;color:var(--ink)}
.rule{width:80px;height:4px;background:var(--navy)}

/* Services */
.tile{top:846px;width:294px;height:294px}
.tile-label{position:absolute;left:0;right:0;bottom:0;padding:14px 10px;text-align:center;color:var(--white);font-size:22px;font-weight:700;background:rgba(20,22,40,.55)}
.tile-feature{background:linear-gradient(180deg,#d5a548,#c89538)}
.tile-feature .feature-text{position:absolute;left:0;right:0;top:100px;text-align:center;color:var(--white);font-size:23px;font-weight:700;line-height:30px}
.tile-feature .btn-outline{position:absolute;left:70px;top:183px;width:152px;height:40px;border:2px solid var(--white);color:var(--white);font-size:15px;font-weight:700;display:flex;align-items:center;justify-content:center}

/* About */
.about-title{left:585px;top:1272px;font-size:36px;font-weight:700;color:var(--ink)}
.about-rule{left:585px;top:1322px}
.about-text{left:582px;top:1348px;width:520px;font-family:"Open Sans",Arial,sans-serif;font-size:16.5px;line-height:27px;color:var(--text)}
.about-text p+p{margin-top:27px}
.btn-learn{left:578px;top:1543px;width:186px;height:49px;font-size:18px}

/* Gallery */
.gallery-title{color:var(--gold)}
.photo{width:388px}

/* Contact */
.contact{left:0;top:2388px;width:1200px;height:682px;background:linear-gradient(180deg,#e4e7f4,#dfe3f1)}
.contact-name{left:0;width:1200px;top:2556px;text-align:center;font-size:20px;font-weight:700;color:var(--ink)}
.contact-phone{left:0;width:1200px;top:2584px;text-align:center;font-size:28px;font-weight:700;color:var(--ink)}
.field{background:var(--white);border:2px solid var(--field-border);font-size:17px;color:#333;padding:0 20px;display:flex;align-items:center}
.field-message{align-items:flex-start;padding-top:20px}
.btn-submit{left:505px;top:2934px;width:207px;height:53px;font-size:19px}

/* Footer */
.footer-brand{left:172px;top:3158px;font-size:40px;line-height:42px;color:var(--ink);font-weight:700}
.footer-links{font-size:13.5px;font-weight:700;color:var(--ink);line-height:26px}
.footer-social{left:876px;top:3160px}
.footer-social i{background:var(--ink);width:18px;height:18px}
.copy{left:876px;top:3210px;font-size:13px;color:var(--ink);line-height:26px}
</style>
</head>
<body>

<!-- Hero -->
<div class="abs hero" role="img" aria-label="Night skyline of a modern city with a tall arched tower lit in purple"></div>
<div class="abs brand"><span>K &amp; M</span><span style="font-weight:400;font-size:34px">STUDIO</span></div>
<div class="abs social hero-social"><i></i><i></i><i></i><i></i></div>
<div class="abs lang">ENG
  <svg width="14" height="9" viewBox="0 0 14 9"><path d="M1 1l6 6 6-6" stroke="#fff" stroke-width="2" fill="none"/></svg>
</div>
<nav class="abs nav">
  <span class="active">HOME</span><span>ABOUT US</span><span>ARCHITECTURE</span><span>INTERIOR DESIGN</span><span>PROJECT MANAGEMENT</span><span>IMPORTING FROM ABROAD</span>
</nav>
<svg class="abs" style="left:88px;top:342px" width="30" height="56" viewBox="0 0 30 56"><path d="M28 2L3 28l25 26" stroke="rgba(255,255,255,.8)" stroke-width="2" fill="none"/></svg>
<svg class="abs" style="left:1110px;top:342px" width="30" height="56" viewBox="0 0 30 56"><path d="M2 2l25 26L2 54" stroke="rgba(255,255,255,.8)" stroke-width="2" fill="none"/></svg>
<div class="abs welcome">WELCOME TO</div>
<div class="abs hero-title">K &amp; M STUDIO</div>
<div class="abs btn btn-start">GET STARTED</div>
<svg class="abs hero-curve" width="1200" height="125" viewBox="0 0 1200 125">
  <path d="M0 122 L600 13 L1200 122 L1200 125 L0 125 Z" fill="#fff"/>
  <path d="M50 124 L600 22 L1150 124" stroke="#1d2240" stroke-width="5" fill="none"/>
</svg>

<!-- Services -->
<div class="abs heading" style="top:748px">OUR SERVICES</div>
<div class="abs rule" style="left:558px;top:798px"></div>

<div class="abs tile" style="left:0;background:linear-gradient(135deg,#8a8f96,#3c63b8)" role="img" aria-label="Modern building with a perforated metal facade">
  <div class="tile-label">ARCHITECTURE</div>
</div>
<div class="abs tile" style="left:302px;background:linear-gradient(180deg,#5a4a34,#2c2620)" role="img" aria-label="Ornate arched interior with striped stone arches">
  <div class="tile-label">INTERIOR DESIGN</div>
</div>
<div class="abs tile tile-feature" style="left:604px" role="img" aria-label="Engineers reviewing plans on a construction site">
  <div class="feature-text">PROJECT<br>MANAGEMENT</div>
  <div class="btn-outline">CLICK HERE</div>
</div>
<div class="abs tile" style="left:906px;width:294px;background:linear-gradient(180deg,#5b5670,#2a2840 60%,#1a1a28)" role="img" aria-label="Container port with cranes at dusk">
  <div class="tile-label">IMPORTING FROM<br>ABROAD</div>
</div>

<!-- About -->
<svg class="abs" style="left:118px;top:1198px" width="406" height="468" viewBox="0 0 406 468" role="img" aria-label="Hands drafting architectural plans with a ruler and pencil">
  <defs><linearGradient id="planTone" x1="0" y1="0" x2="1" y2="1"><stop offset="0" stop-color="#d9dbdc"/><stop offset="1" stop-color="#a9b6c0"/></linearGradient></defs>
  <polygon points="203,0 406,117 406,351 203,468 0,351 0,117" fill="url(#planTone)"/>
</svg>
<div class="abs about-title">ABOUT US</div>
<div class="abs rule about-rule"></div>
<div class="abs about-text">
  <p>Fusce tellus Sed metus augue convallis et vehicula ut pulvinar eu ante Integer orci tellus tristique vitae consequat nec</p>
  <p>Aorta vel lectus Nulla sit amet enim Proin dui lectus cursus eu mattis laoreet viverra sit amet quam Curabitur vel dolor ultrices ipsum dictum tristique Praesent vitae lacus Ut velit e</p>
</div>
<div class="abs btn btn-learn">LEARN MORE</div>

<!-- Gallery -->
<div class="abs heading gallery-title" style="top:1727px">OUR GALLERY</div>
<div class="abs rule" style="left:551px;top:1776px"></div>

<div class="abs photo" style="left:0;top:1830px;height:280px;background:linear-gradient(180deg,#8fa7c4,#c9a27a 70%,#6a6a6a)" role="img" aria-label="City avenue with palm trees and glass towers"></div>
<div class="abs photo" style="left:396px;top:1830px;width:398px;height:280px;background:linear-gradient(135deg,#5d8fd0,#c7b79a 55%,#3c6a78)" role="img" aria-label="Geometric glass lattice facade against blue sky"></div>
<div class="abs photo" style="left:803px;top:1830px;width:397px;height:280px;background:radial-gradient(circle at 42% 35%,#cfe2ea,#9a8f80 45%,#4e4a46)" role="img" aria-label="Spiral interior ceiling with a round skylight"></div>
<div class="abs photo" style="left:0;top:2118px;height:270px;background:linear-gradient(180deg,#6fa4d8,#2f7fb0 55%,#58605a)" role="img" aria-label="Blue glass office towers beside a road"></div>
<div class="abs photo" style="left:396px;top:2118px;width:398px;height:270px;background:linear-gradient(180deg,#e07a22,#f0a040 60%,#f3e6d4)" role="img" aria-label="Long corridor of orange arches"></div>
<div class="abs photo" style="left:803px;top:2118px;width:397px;height:270px;background:linear-gradient(180deg,#1d2244,#2d3a5a 55%,#4e7a52)" role="img" aria-label="Mosque with green dome and minaret at night"></div>

<!-- Contact -->
<div class="abs contact" role="img" aria-label="Faded city skyline backdrop"></div>
<div class="abs heading" style="top:2458px">CONTACT US</div>
<div class="abs rule" style="left:558px;top:2506px"></div>
<div class="abs contact-name">K &amp; M STUDIO</div>
<div class="abs contact-phone">(555) 013 2870</div>

<div class="abs field" style="left:195px;top:2653px;width:393px;height:53px">Name</div>
<div class="abs field" style="left:605px;top:2653px;width:393px;height:53px">Phone Number</div>
<div class="abs field" style="left:195px;top:2719px;width:393px;height:53px">Email address</div>
<div class="abs field" style="left:605px;top:2719px;width:393px;height:53px">Subject</div>
<div class="abs field field-message" style="left:195px;top:2790px;width:803px;height:121px">Message</div>
<div class="abs btn btn-submit">SUBMIT NOW</div>

<!-- Footer -->
<div class="abs footer-brand">K &amp; M<br><span style="font-weight:400">STUDIO</span></div>
<div class="abs footer-links" style="left:421px;top:3158px">HOME<br>ABOUT US<br>ARCHITECTURE<br>INTERIOR DESIGN</div>
<div class="abs footer-links" style="left:612px;top:3160px">PROJECT MANAGEMENT<br>IMPORTING FROM ABROAD<br>CONTACT US</div>
<div class="abs social footer-social"><i></i><i></i><i></i><i></i></div>
<div class="abs copy">© 2019 Company Name<br>All right reserved &nbsp;|&nbsp; Privacy Policy</div>

</body>
</html>
```